Woman owned consulting company needs an elegant and modern business card design

I need a business card design for my new consulting company, Mara Quillon Consulting. I am looking for something that is simple and elegant, but also creative and original. You can use either version of the logo that are attached. I have also included the information that needs to be featured on the business card.

Contact Information for Business Card

Requirements
Must have
• The logo and the font type and a standard business card size. Use shades of gray/silver and or rose gold that are in the logo.
• I didn't realize that my actual logo wasn't attached. Please incorporate in the designs.
Should not have
• Colors that are different from my logo

```html
<!DOCTYPE html>
<html lang="en">
<head>
<meta charset="utf-8">
<title>Mara Quillon Consulting — Business Card</title>
<link href="https://fonts.googleapis.com/css2?family=Arimo:wght@400&display=swap" rel="stylesheet">
<style>
  :root {
    --backdrop: #d9d9db;
    --card-white: #f7f7f6;
    --rose: #c94a7a;
    --rose-soft: #e06e9b;
    --rose-text: #d4437a;
    --slate: #6f7178;
    --shadow: rgba(40, 40, 45, 0.28);
  }
  * { margin: 0; padding: 0; box-sizing: border-box; }
  html, body {
    width: 1200px;
    height: 787px;
    overflow: hidden;
    background: var(--backdrop);
    font-family: "Arimo", Arial, sans-serif;
  }
  .sheet {
    width: 1200px;
    height: 787px;
    display: flex;
    align-items: center;
    justify-content: center;
    gap: 60px;
  }
  .card {
    width: 525px;
    height: 300px;
    border-radius: 16px;
    position: relative;
    box-shadow: 0 6px 18px var(--shadow);
    text-transform: uppercase;
    letter-spacing: 0.02em;
  }
  .card--front { background: var(--card-white); }
  .card--back { background: var(--rose); }

  .identity {
    position: absolute;
    top: 48px;
    left: 44px;
    font-size: 14px;
  }
  .identity__name { color: var(--rose-text); }
  .identity__divider,
  .identity__role { color: var(--slate); }
  .identity__divider { margin: 0 6px; }

  .contact {
    position: absolute;
    left: 44px;
    bottom: 60px;
    font-size: 11.5px;
    line-height: 1.7;
  }
  .contact__line { color: var(--slate); }
  .contact__divider { margin: 0 6px; }
  .contact__web { color: var(--rose-text); }

  .brand-name {
    position: absolute;
    right: 40px;
    bottom: 38px;
    font-size: 26px;
    color: var(--slate);
    letter-spacing: 0.04em;
  }

  .back-company {
    position: absolute;
    left: 44px;
    bottom: 60px;
    font-size: 18px;
    color: var(--rose-soft);
    letter-spacing: 0.03em;
  }
</style>
</head>
<body>
  <main class="sheet">
    <section class="card card--front" aria-label="Business card front">
      <p class="identity">
        <span class="identity__name">Mara Quillon</span><span class="identity__divider">|</span><span class="identity__role">Owner</span>
      </p>
      <div class="contact">
        <p class="contact__line">555-014-2273<span class="contact__divider">|</span>mara@maraquillonconsulting.com</p>
        <p class="contact__web">www.maraquillonconsulting.com</p>
      </div>
      <p class="brand-name">MQC</p>
    </section>

    <section class="card card--back" aria-label="Business card back">
      <p class="back-company">Mara Quillon Consulting, LLC</p>
    </section>
  </main>
</body>
</html>
```